Web site for new fundraising service for charities

We need a web design for a new charitable trust based in New Zealand. With the economic downturn, charities are finding it increasingly difficult to raise the monies they need to deliver their services.

Using a network of fundraisers working out of their homes, KindLoop (our charitable trust) will source unique, high interest auction items on behalf of multiple charities - things like luxury cruises, exotic travel, luxury accommodation, fine dining, unique experiences with sports and entertainment personalities, tickets to sporting and entertainment events, etc.

Once we have sourced sufficient high value items we will then partner with BidNest (NZ's equivalent of uLot) to launch the auction. The proceeds from each auction will benefit up to 6 charities. The auctions will be promoted through BidNest, through PR, and through the communications channels of the benefiting charities, reaching a wider audience than would be possible if just one charity was holding an auction and therefore resulting in more competitive bidding and higher returns for the charities.

We need a web site that we can point potential donors of auction items to, that gives them confidence in KindLoop. We will also leverage the web site with journalists. And of course, charities who are wondering whether or not to use KindLoop will come to our web site and check out our credentials. The tone of the site needs to be warm, friendly, approachable.

We are not locked into the blue and orange colors of the logo and in fact are experimenting with other colors as we speak.

Please note that what we're looking for is the design for the home page, plus a sub page design.

CEOs, corporate social responsibility managers, general managers, business owners, charities, the media

Communications

• Video on home page
Newsletter sign up on all pages
Navigation as per the attached PDF example

```html
<!DOCTYPE html>
<html lang="en">
<head>
<meta charset="utf-8">
<title>KindLoop — Home</title>
<link href="https://fonts.googleapis.com/css2?family=Questrial&family=Arimo:wght@400;700&family=Oswald:wght@500&display=swap" rel="stylesheet">
<style>
:root{
  --orange:#f07c12;
  --orange-light:#f0a860;
  --orange-deep:#ea6f08;
  --dark:#1b1b1b;
  --dark-2:#2b2b2e;
  --grey-panel:#eeeeee;
  --grey-text:#8a8a8a;
  --quote-bg:#6a6a6a;
  --white:#ffffff;
  --ink:#1a1a1a;
  --red-bar:#8c1a1a;
}
*{box-sizing:border-box;margin:0;padding:0}
html,body{width:1200px;height:872px;overflow:hidden;background:var(--dark)}
body{font-family:"Questrial",sans-serif;color:var(--white)}
.page{position:relative;width:1200px;height:872px;overflow:hidden}
.backdrop{position:absolute;inset:0;background:
  radial-gradient(ellipse at 70% 30%,#4a4038 0%,transparent 60%),
  radial-gradient(ellipse at 20% 70%,#3c3a36 0%,transparent 55%),
  linear-gradient(180deg,#2a2826 0%,#3a3531 50%,#24211f 100%)}
.top-rule{position:absolute;left:0;top:0;width:1200px;height:3px;background:var(--orange)}

/* sidebar */
.sidebar{position:absolute;left:131px;top:0;width:224px;height:639px}
.brand{height:120px;background:#2a2a2a;border:1px solid #555;display:flex;flex-direction:column;align-items:center;justify-content:center;gap:8px}
.brand-dot{width:30px;height:30px;border-radius:50%;background:#d8d8d8}
.brand-name{font-size:32px;color:#d8d8d8;letter-spacing:.5px}
.sidebar-body{position:absolute;top:120px;left:0;width:224px;height:519px;
  background:linear-gradient(180deg,var(--orange-light) 0%,#ef9a48 40%,var(--orange) 100%);
  clip-path:polygon(0 0,100% 0,100% 100%,50% 91.3%,0 100%)}
.main-nav{position:absolute;top:50px;left:0;width:224px;list-style:none}
.main-nav li{height:40px;display:flex;align-items:center;padding-left:20px;font-size:15px;letter-spacing:-.3px;text-transform:uppercase;white-space:nowrap}
.main-nav li + li{margin:0 18px 0 20px;padding-left:0;border-bottom:1px dotted rgba(120,60,10,.45)}
.main-nav li.current{background:var(--dark);height:37px}
.call{position:absolute;top:370px;left:21px;color:var(--ink);white-space:nowrap}
.call-label{font-size:28px;line-height:1;letter-spacing:-1px}
.call-number{font-size:33px;line-height:1.1;margin-top:4px;letter-spacing:-1.5px}

/* header */
.social{position:absolute;top:25px;left:943px;display:flex;gap:9px}
.social span{width:36px;height:36px;border-radius:50%;background:#c9c9c9;display:block}
.top-nav{position:absolute;top:88px;left:690px;display:flex;align-items:center;font-size:21px;text-transform:uppercase;letter-spacing:-.8px;white-space:nowrap}
.top-nav a{color:var(--white);text-decoration:none}
.top-nav .sep{width:1px;height:12px;border-left:1px dotted #aaa;margin:0 21px}

/* video */
.video{position:absolute;left:372px;top:143px;width:436px;height:313px;background:var(--dark-2);border:1px solid #444;padding:5px}
.video-frame{position:relative;width:426px;height:266px;background:linear-gradient(180deg,#8aa2bb 0%,#6c7b86 35%,#5f6a5b 60%,#474a3e 100%)}
.play-big{position:absolute;left:183px;top:120px}
.controls{display:flex;align-items:center;height:38px;padding:0 2px;gap:8px;font-size:13px;white-space:nowrap}
.controls > *{flex-shrink:0}
.track{width:186px;height:7px;background:#111;border:1px solid #333;position:relative}
.track::before{content:"";position:absolute;left:0;top:0;height:100%;width:68%;background:var(--red-bar)}
.time .total{color:#888}
.vol{width:36px;height:6px;background:var(--red-bar)}
.hd{margin-left:auto;font-family:"Arimo",sans-serif;font-weight:700;font-style:italic;font-size:18px;color:#ddd;border-left:2px solid #111;padding-left:8px;display:flex;align-items:center;gap:5px}

/* subscribe */
.subscribe{position:absolute;left:830px;top:143px;width:239px;height:313px;background:linear-gradient(180deg,#fff 0%,var(--grey-panel) 100%);border:1px solid #ccc}
.subscribe-title{position:absolute;left:-6px;top:10px;width:251px;height:47px;background:linear-gradient(180deg,#f6a54f,var(--orange-deep));font-family:"Oswald",sans-serif;font-size:30px;padding-left:10px;line-height:45px;color:#fff}
.subscribe-copy{position:absolute;top:62px;left:12px;width:215px;font-family:"Arimo",sans-serif;font-size:12.5px;line-height:15px;color:var(--grey-text);text-align:center}
.field{position:absolute;left:12px;display:flex;align-items:center;font-family:"Arimo",sans-serif;font-size:11.5px;color:#111;white-space:nowrap}
.field label{width:74px}
.field span{width:143px;height:21px;background:#fff;border:1px solid #bbb;font-size:11.5px;color:#aaa;padding:3px 4px;overflow:hidden}
.submit{position:absolute;left:81px;top:272px;width:92px;height:29px;background:linear-gradient(180deg,#555,#222);color:#fff;font-size:16px;text-align:center;line-height:29px;border-radius:2px}

/* quote */
.divider{position:absolute;top:481px;left:428px;width:601px;border-top:1px dotted #999}
.quote-heading{position:absolute;top:498px;left:381px;font-size:23px;font-weight:400;letter-spacing:-.8px;text-transform:uppercase;white-space:nowrap}
.quote{position:absolute;top:538px;left:378px;width:691px;height:81px;background:var(--quote-bg);display:flex}
.quote-photo{width:179px;height:81px;flex-shrink:0;background:linear-gradient(135deg,#c9c2b0 0%,#efeee6 45%,#9fa58a 100%)}
.quote-text{padding:17px 12px 0 12px;font-size:12px;line-height:15px}

/* newsletter */
.newsletter{position:absolute;top:682px;left:173px;display:flex;align-items:center}
.newsletter-title{font-size:36px;letter-spacing:-2.5px;text-transform:uppercase;width:232px;white-space:nowrap;flex-shrink:0}
.newsletter-input{width:464px;height:32px;flex-shrink:0;background:linear-gradient(180deg,#fff,#e6e9ee);border-radius:3px;font-family:"Arimo",sans-serif;font-style:italic;color:#777;font-size:14px;padding:8px 11px}
.signup{margin-left:12px;width:125px;height:34px;flex-shrink:0;background:linear-gradient(180deg,#f98b2a,#ee5f05);border:1px solid #fff;font-size:18px;letter-spacing:-.5px;text-align:center;line-height:32px;text-transform:uppercase}

/* footer */
.footer{position:absolute;top:757px;left:0;width:1200px;height:110px;background:var(--orange);text-align:center;font-size:13px;letter-spacing:-.2px;white-space:nowrap}
.footer-links{margin-top:26px}
.footer-links a{color:var(--white);text-decoration:none}
.footer-links i{font-style:normal;margin:0 6px}
.footer-contact{margin-top:6px}
.footer-copy{margin-top:7px}
.footer-mark{position:absolute;left:982px;top:28px;width:60px;height:60px;border-radius:50%;background:rgba(150,130,110,.35)}
.footer-base{position:absolute;top:867px;left:0;width:1200px;height:5px;background:#2a2a2a}
</style>
</head>
<body>
<div class="page">
  <div class="backdrop" role="img" aria-label="Darkened collage of luxury travel, cruise, dining and event photographs"></div>
  <div class="top-rule"></div>

  <aside class="sidebar">
    <div class="brand">
      <span class="brand-dot"></span>
      <span class="brand-name">KindLoop</span>
    </div>
    <div class="sidebar-body">
      <ul class="main-nav">
        <li class="current">Home</li>
        <li>How it works</li>
        <li>Acts of goodness</li>
        <li>Goodness partners</li>
        <li>About us</li>
        <li>Contact us</li>
      </ul>
      <div class="call">
        <div class="call-label">CALL US:</div>
        <div class="call-number">000-123-4567</div>
      </div>
    </div>
  </aside>

  <div class="social" aria-label="Social links">
    <span aria-label="Social network one"></span>
    <span aria-label="Social network two"></span>
    <span aria-label="Social network three"></span>
  </div>

  <nav class="top-nav">
    <a href="#">Donors</a><span class="sep"></span>
    <a href="#">Charities</a><span class="sep"></span>
    <a href="#">Auctions</a>
  </nav>

  <section class="video">
    <div class="video-frame" role="img" aria-label="Video still of a rooftop terrace with lounge seating among city towers">
      <svg class="play-big" width="60" height="60" viewBox="0 0 60 60"><circle cx="30" cy="30" r="29" fill="#222" fill-opacity=".85"/><path d="M24 18 L42 30 L24 42Z" fill="#ddd"/></svg>
    </div>
    <div class="controls">
      <svg width="16" height="18" viewBox="0 0 16 18"><path d="M1 1 L15 9 L1 17Z" fill="#fff"/></svg>
      <div class="track"></div>
      <span class="time">1:26 / <span class="total">3:22</span></span>
      <svg width="16" height="16" viewBox="0 0 16 16"><path d="M0 5h5l6-5v16l-6-5H0z" fill="#fff"/></svg>
      <div class="vol"></div>
      <div class="hd"><svg width="24" height="16" viewBox="0 0 24 16"><rect x="2" y="2" width="20" height="12" fill="none" stroke="#ddd" stroke-width="2"/></svg>HD</div>
    </div>
  </section>

  <section class="subscribe">
    <div class="subscribe-title">Subscribe</div>
    <p class="subscribe-copy">Charity auctions are a great way to get luxury items and unique experiences while helping a worthwhile cause. Subscribe to our email list to be kept informed about upcoming auctions.</p>
    <div class="field" style="top:145px"><label>First Name:</label><span></span></div>
    <div class="field" style="top:176px"><label>Last Name:</label><span></span></div>
    <div class="field" style="top:206px"><label>Email:</label><span>e.g. name@kindloop.nz</span></div>
    <div class="field" style="top:237px"><label>City:</label><span></span></div>
    <div class="submit">SUBMIT</div>
  </section>

  <div class="divider"></div>
  <h2 class="quote-heading">Inspiration Quote</h2>
  <section class="quote">
    <div class="quote-photo" role="img" aria-label="Fine dining table with plated dishes and glassware"></div>
    <p class="quote-text">Lorem Ipsum is simply dummy text of the printing and typesetting industry. Lorem Ipsum has been the industry’s standard dummy text ever since the 1500s, when an unknown printer took a galley of type and scrambled.</p>
  </section>

  <section class="newsletter">
    <div class="newsletter-title">Newsletter!</div>
    <div class="newsletter-input">Enter Email Here...</div>
    <div class="signup">Sign Up!</div>
  </section>

  <footer class="footer">
    <div class="footer-links">
      <a href="#">Home</a><i>|</i><a href="#">Affiliate</a><i>|</i><a href="#">Our Terms of Use</a><i>|</i><a href="#">Privacy Policy</a><i>|</i><a href="#">Return Policy</a><i>|</i><a href="#">Shipping Policy</a><i>|</i><a href="#">Cart</a><i>|</i><a href="#">Contact Us</a>
    </div>
    <div class="footer-contact">Tel: 000-123-4567. Address: 48 Harbour Lane, Ste 3, Wellington 6011.</div>
    <div class="footer-copy">© 2012 KindLoop. All Rights Reserved.</div>
    <span class="footer-mark"></span>
  </footer>
  <div class="footer-base"></div>
</div>
</body>
</html>
```